Redesign and move to Wordpress for corvandel.com

Our website needs a redesign and at the same time we are moving it to Wordpress. Please help us with a new digital professional look and feel.

We are an Australian Software Engineering company specialising in advanced software development using in A.I., PLatform Engineering, Integration and Cloud. See the current corvandel.com for more information about us.

```html
<!DOCTYPE html>
<html lang="en">
<head>
<meta charset="utf-8">
<title>Corvandel — AI, Cloud and Integrated Solutions</title>
<link href="https://fonts.googleapis.com/css2?family=Rubik:wght@500;600;700&family=Roboto:wght@400;500;700&display=swap" rel="stylesheet">
<style>
:root{
  --navy:#04132a;
  --navy-2:#0a1f3f;
  --blue:#0b4a94;
  --blue-bright:#0f5fc4;
  --teal:#2ac2c0;
  --ink:#1a1a1a;
  --muted:#555;
  --grey:#e3e3e3;
  --light:#f1f2f4;
  --white:#fff;
}
*{box-sizing:border-box;margin:0;padding:0}
html,body{width:1200px;height:4399px;overflow:hidden}
body{font-family:"Roboto",sans-serif;color:var(--ink);background:var(--white);position:relative}
.section{position:absolute;left:0;width:1200px;overflow:hidden}
.abs{position:absolute}
h1,h2,h3,.heading{font-family:"Rubik",sans-serif}
.btn{position:absolute;background:var(--blue);color:var(--white);font-family:"Rubik",sans-serif;font-weight:600;font-size:14px;letter-spacing:.5px;display:flex;align-items:center;justify-content:center;border-radius:3px}
.eyebrow{font-family:"Rubik",sans-serif;font-weight:500;font-size:17px;color:#222;text-transform:uppercase}
.section-title{font-family:"Rubik",sans-serif;font-weight:700;font-size:36px;color:var(--blue);letter-spacing:1px;text-transform:uppercase}
.centered{position:absolute;left:0;width:1200px;text-align:center}

/* hero */
.hero{top:0;height:556px;background:radial-gradient(circle at 78% 45%,#0f3a6e 0,#061a36 30%,var(--navy) 60%)}
.brand{display:flex;align-items:center;gap:12px;color:var(--white);font-family:"Rubik",sans-serif;font-weight:500;font-size:30px;letter-spacing:1px}
.brand-square{width:26px;height:26px;border:3px solid var(--white)}
.nav{top:38px;left:438px;display:flex;font-size:15px;color:var(--white)}
.nav a{color:inherit;text-decoration:none;margin-right:36px}
.nav a.active{color:var(--teal)}
.nav-active-bar{top:17px;left:438px;width:44px;height:2px;background:var(--teal)}
.search{position:absolute;top:32px;left:927px;width:162px;height:34px;border:1px solid #5d6c84;display:flex}
.search span{flex:1;font-size:12px;color:#9aa5b5;padding:10px 12px}
.search i{width:32px;background:var(--blue-bright);display:flex;align-items:center;justify-content:center}
.hero h1{top:140px;left:110px;width:560px;font-size:41px;line-height:52px;color:var(--white);font-weight:700;text-transform:uppercase;letter-spacing:.5px}
.hero h1 em{font-style:normal;color:var(--teal)}
.hero-art{top:120px;left:760px;width:340px;height:350px;border-radius:50%;background:radial-gradient(circle,#1d6fd6 0,#0c3a78 35%,rgba(4,19,42,0) 70%)}

/* about */
.about{top:556px;height:646px;background:var(--white)}
.photo{position:absolute}
.about-rule{top:205px;left:862px;width:180px;height:2px;background:var(--teal)}
.about-dot{top:200px;left:858px;width:12px;height:12px;border-radius:50%;background:var(--white);border:3px solid var(--teal)}
.about p{top:242px;left:662px;width:428px;font-size:16px;line-height:31px;color:#222}

/* services */
.services{top:1202px;height:658px;background:linear-gradient(110deg,#0a3a86 0,#0c50b2 55%,#1a5fc2 100%)}
.services .section-title{color:var(--white)}
.svc{position:absolute;width:237px;height:173px;border:1px solid rgba(255,255,255,.45);color:var(--white);display:flex;flex-direction:column;align-items:center;justify-content:flex-end;padding-bottom:26px;text-align:center;font-size:18px;line-height:25px;font-weight:500}
.svc.active{border:3px solid var(--white)}
.svc svg{margin-bottom:14px}

/* clients */
.clients{top:1860px;height:437px;background:var(--light)}
.client{position:absolute;top:237px;width:228px;height:108px;background:var(--white);border:1px solid #d8d8d8;border-radius:4px;display:flex;align-items:center;justify-content:center;font-family:"Roboto",sans-serif;font-weight:700;font-size:28px;color:#6d6d6d}
.client.raised{box-shadow:0 6px 14px rgba(0,0,0,.18)}

/* news */
.news{top:2297px;height:693px;background:var(--grey)}
.card{position:absolute;top:176px;width:302px;height:430px;background:var(--white);box-shadow:0 2px 8px rgba(0,0,0,.12)}
.card.active{border-bottom:6px solid var(--blue);height:436px}
.card .img{height:215px}
.card .meta{padding:18px 22px 0;font-size:12.5px;line-height:20px;color:var(--blue)}
.card h3{padding:8px 22px 0;font-family:"Roboto",sans-serif;font-size:15px;font-weight:700;color:#222;text-transform:uppercase}
.card p{padding:8px 22px 0;font-size:12.5px;line-height:22px;color:#555}
.arrow{position:absolute;top:370px;width:46px;height:46px;border-radius:50%;background:var(--white);border:2px solid #222;display:flex;align-items:center;justify-content:center}

/* newsletter */
.newsletter{top:2990px;height:368px;background:var(--navy)}
.nl-art{top:20px;left:80px;width:440px;height:330px;background:radial-gradient(circle,#1a5fc2 0,#0b2e66 35%,rgba(4,19,42,0) 70%)}
.newsletter .label{top:72px;left:598px;font-family:"Rubik",sans-serif;font-weight:600;font-size:18px;color:var(--white)}
.newsletter h2{top:110px;left:598px;width:520px;font-size:31px;line-height:41px;color:var(--white);font-weight:700;text-transform:uppercase;letter-spacing:.5px}
.nl-input{top:250px;left:598px;width:327px;height:42px;background:var(--white);font-size:13px;color:#666;padding:13px 30px}
.nl-btn{top:250px;left:925px;width:163px;height:42px;border-radius:0;background:var(--blue-bright)}

/* contact */
.contact{top:3358px;height:560px;background:#f2f3f5}
.contact-photo{top:210px;left:0;width:500px;height:350px;background:linear-gradient(90deg,#cfd6de,#e9eef3 60%,#b9c6d4)}
.contact h2{top:92px;left:112px;font-size:32px;color:var(--blue);font-weight:700}
.info{left:112px;display:flex;gap:14px;align-items:flex-start}
.info .ico{width:30px;height:30px;border-radius:50%;background:var(--blue);display:flex;align-items:center;justify-content:center;margin-top:4px}
.info b{display:block;font-size:13px;font-weight:700}
.info span{font-size:13px;color:#444}
.form-panel{top:65px;left:500px;width:700px;height:495px;background:var(--white);border-top:3px solid var(--blue);border-left:3px solid var(--blue)}
.form-panel h2{top:60px;left:42px;font-size:32px;color:var(--blue);font-weight:700}
.field{position:absolute;height:50px;border:1px solid #cfcfcf;font-size:13px;color:#555;padding:17px 18px}
.form-btn{top:389px;left:42px;width:542px;height:40px;font-size:13px;border-radius:0}

/* footer */
.footer{top:3918px;height:481px;background:var(--blue)}
.footer .brand{font-size:44px}
.footer .brand-square{width:40px;height:40px;border-width:5px}
.social{top:258px;left:175px;display:flex;gap:12px}
.social i{width:32px;height:32px;border-radius:50%;background:var(--white);display:block}
.footer h3{font-size:20px;font-weight:600;color:var(--white);text-transform:uppercase;letter-spacing:.5px}
.links{top:144px;left:457px;list-style:none;color:var(--white);font-size:16px;line-height:31px}
.ft-text{top:144px;left:665px;width:420px;color:var(--white);font-size:16px;line-height:31px}
.ft-input{top:207px;left:665px;width:422px;height:52px;background:var(--white);font-size:14px;color:#444;padding:18px 24px}
.ft-btn{top:276px;left:665px;width:171px;height:46px;background:var(--white);color:var(--blue);border-radius:0}
.ft-rule{top:365px;left:112px;width:976px;height:1px;background:rgba(255,255,255,.4)}
.ft-legal{top:390px;font-size:14px;color:var(--white)}
.ft-copy{top:432px;font-size:14px;color:var(--white)}
</style>
</head>
<body>

<header class="section hero">
  <div class="abs brand" style="top:28px;left:110px"><span class="brand-square"></span>corvandel</div>
  <div class="abs nav-active-bar"></div>
  <nav class="abs nav"><a class="active">Home</a><a>About Us</a><a>Our Services</a><a>Blog</a><a>Contact Us</a></nav>
  <div class="search"><span>Search..</span><i><svg width="14" height="14" viewBox="0 0 14 14"><circle cx="6" cy="6" r="4.5" fill="none" stroke="#fff" stroke-width="1.6"/><line x1="9.3" y1="9.3" x2="13" y2="13" stroke="#fff" stroke-width="1.6"/></svg></i></div>
  <h1 class="abs">Building the future of technology <em>with AI, cloud,</em> and integrated solutions</h1>
  <div class="btn" style="top:372px;left:110px;width:384px;height:42px">BOOK AN OBLIGATION FREE CONSULTATION</div>
  <div class="abs hero-art" role="img" aria-label="Glowing blue processor chip on a circuit board"></div>
</header>

<section class="section about">
  <div class="photo" style="top:86px;left:111px;width:224px;height:152px;background:linear-gradient(135deg,#0f2a4a,#d08a3e)" role="img" aria-label="Human hand reaching toward a robot hand under an AI chip"></div>
  <div class="photo" style="top:276px;left:111px;width:224px;height:302px;background:linear-gradient(180deg,#1b2a6e,#4b3a9e 60%,#c44fa0)" role="img" aria-label="Futuristic city skyline lit in neon"></div>
  <div class="photo" style="top:86px;left:372px;width:225px;height:303px;background:linear-gradient(180deg,#0b2d68,#1b7fd6 55%,#0a1b3a)" role="img" aria-label="Digital cloud hovering over a keyboard"></div>
  <div class="photo" style="top:426px;left:372px;width:225px;height:152px;background:linear-gradient(135deg,#1d2b40,#4a6a8e)" role="img" aria-label="Engineers working at monitors in an operations room"></div>
  <div class="abs eyebrow" style="top:150px;left:660px">Who we are</div>
  <h2 class="abs section-title" style="top:184px;left:660px">About us</h2>
  <div class="abs about-rule"></div><div class="abs about-dot"></div>
  <p class="abs">At Corvandel, we craft bespoke software solutions that are not available on the market. By building organizations integration products, process automation, legacy system enablement, or advanced intelligent systems, we empower our customers to achieve a competitive edge in their industry.</p>
  <div class="btn" style="top:449px;left:662px;width:152px;height:43px">LEARN &nbsp;MORE</div>
</section>

<section class="section services" role="img" aria-label="Blue-tinted photo of a team working at a laptop">
  <div class="centered eyebrow" style="top:62px;color:#fff">What we do</div>
  <h2 class="centered section-title" style="top:98px">Our services</h2>
  <div class="centered" style="top:152px;font-size:16px;color:#fff">Comprehensive Software Solutions for Every Business Need</div>

  <div class="svc" style="top:213px;left:101px"><svg width="60" height="60" viewBox="0 0 60 60" fill="none" stroke="#fff" stroke-width="2"><circle cx="30" cy="30" r="11"/><circle cx="30" cy="30" r="19" stroke-dasharray="6 4"/><path d="M8 22a24 24 0 0 1 40-8M52 38a24 24 0 0 1-40 8"/></svg>Enterprise<br>Systems Integration</div>
  <div class="svc active" style="top:213px;left:354px"><svg width="60" height="60" viewBox="0 0 60 60" fill="none" stroke="#fff" stroke-width="2"><circle cx="30" cy="30" r="8"/><circle cx="30" cy="10" r="4"/><circle cx="30" cy="50" r="4"/><circle cx="10" cy="30" r="4"/><circle cx="50" cy="30" r="4"/><circle cx="16" cy="16" r="3"/><circle cx="44" cy="44" r="3"/><circle cx="44" cy="16" r="3"/><circle cx="16" cy="44" r="3"/></svg>Micro<br>Services</div>
  <div class="svc" style="top:213px;left:607px"><svg width="60" height="60" viewBox="0 0 60 60" fill="none" stroke="#fff" stroke-width="2"><rect x="12" y="36" width="36" height="16"/><rect x="20" y="20" width="20" height="16"/><line x1="30" y1="6" x2="30" y2="20"/><line x1="6" y1="52" x2="54" y2="52"/></svg>Platform<br>Engineering</div>
  <div class="svc" style="top:213px;left:860px"><svg width="60" height="60" viewBox="0 0 60 60" fill="none" stroke="#fff" stroke-width="2"><circle cx="26" cy="26" r="11"/><path d="M10 54c2-10 8-14 16-14s14 4 16 14"/><circle cx="46" cy="14" r="8"/></svg>Conversational<br>Ai</div>

  <div class="svc" style="top:402px;left:101px"><svg width="60" height="60" viewBox="0 0 60 60" fill="none" stroke="#fff" stroke-width="2"><rect x="10" y="22" width="34" height="24"/><line x1="27" y1="46" x2="27" y2="54"/><line x1="18" y1="54" x2="36" y2="54"/><path d="M34 18a10 10 0 0 1 18 4a7 7 0 0 1-2 14"/><circle cx="27" cy="34" r="6"/></svg>IPAAS</div>
  <div class="svc" style="top:402px;left:354px"><svg width="60" height="60" viewBox="0 0 60 60" fill="none" stroke="#fff" stroke-width="2"><path d="M20 54V42c-6-4-9-10-9-16a17 17 0 0 1 34 0l4 8h-5v8h-8v12"/><circle cx="28" cy="24" r="5"/></svg>Co Pilot / AI Agents</div>
  <div class="svc" style="top:402px;left:607px;padding-bottom:12px"><svg width="60" height="60" viewBox="0 0 60 60" fill="none" stroke="#fff" stroke-width="2"><rect x="18" y="22" width="24" height="16"/><circle cx="10" cy="14" r="4"/><circle cx="30" cy="8" r="4"/><circle cx="50" cy="14" r="4"/><path d="M12 18l8 6M30 12v10M48 18l-8 6"/><path d="M10 48c8 6 32 6 40 0"/></svg>Real-time Data Stream<br>Processing</div>
  <div class="svc" style="top:402px;left:860px;padding-bottom:12px"><svg width="60" height="60" viewBox="0 0 60 60" fill="none" stroke="#fff" stroke-width="2"><rect x="8" y="8" width="14" height="14"/><rect x="38" y="8" width="14" height="14"/><rect x="23" y="23" width="14" height="14"/><rect x="8" y="38" width="14" height="14"/><rect x="38" y="38" width="14" height="14"/><path d="M22 15h16M15 22v16M45 22v16M22 45h16"/></svg>Custom Integration For<br>Small To Medium Business</div>
</section>

<section class="section clients">
  <div class="centered eyebrow" style="top:76px">Corvandel</div>
  <h2 class="centered section-title" style="top:110px">Our clients</h2>
  <div class="centered" style="top:165px;font-size:16px;color:#222">Tailored Technology Solutions to Meet Unique Business Challenges</div>
  <div class="client" style="left:110px">Meridan</div>
  <div class="client" style="left:361px">Northvale</div>
  <div class="client raised" style="left:611px">Trexford</div>
  <div class="client" style="left:862px">Kestrel Fund</div>
</section>

<section class="section news">
  <div class="centered eyebrow" style="top:64px">Updates from our industry</div>
  <h2 class="centered section-title" style="top:100px">Our news &amp; articles</h2>
  <div class="arrow" style="left:31px"><svg width="20" height="20" viewBox="0 0 20 20" fill="none" stroke="#222" stroke-width="2.4"><path d="M17 10H4M9 4l-6 6 6 6"/></svg></div>
  <div class="arrow" style="left:1122px;border-color:var(--blue)"><svg width="20" height="20" viewBox="0 0 20 20" fill="none" stroke="#0b4a94" stroke-width="2.4"><path d="M3 10h13M11 4l6 6-6 6"/></svg></div>

  <article class="card" style="left:112px">
    <div class="img" style="background:linear-gradient(135deg,#000 30%,#1f5fae 60%,#d85a2a)" role="img" aria-label="Silhouette of a head made of glowing code"></div>
    <div class="meta">10 unexpected ways to use CodeHelm Pilot</div>
    <h3>AI in software engineering</h3>
    <p>(CodeHelm Blog) CodeHelm Pilot is widely known for its code generation feature. Learn how the AI assistant's abilities can extend beyond just code generation.</p>
  </article>
  <article class="card active" style="left:448px">
    <div class="img" style="background:linear-gradient(135deg,#3a3f48,#8c95a0 60%,#c9ced4)" role="img" aria-label="Two developers reviewing code at a desk"></div>
    <div class="meta">How CodeHelm's Developer Experience team improved innerloop development</div>
    <h3>Software development</h3>
    <p>(CodeHelm Blog) CodeHelm's latest solution to the ubiquitous engineering problem of integration testing in a distributed service ecosystem.</p>
  </article>
  <article class="card" style="left:785px">
    <div class="img" style="background:radial-gradient(circle at 50% 40%,#c36ad8 0,#3a4fc8 30%,#0d2a86 70%)" role="img" aria-label="Light bulb filled with glowing network lines"></div>
    <div class="meta">How Storytelling Helps Data-driven Teams Succeed</div>
    <h3>Business insights</h3>
    <p>(Harbor School of Management) Winning leaders know that data alone isn't enough. It's the art of storytelling that drives sustained performance.</p>
  </article>
</section>

<section class="section newsletter">
  <div class="abs nl-art" role="img" aria-label="Glowing processor chip with circuit traces"></div>
  <div class="abs label">REGISTER TO OUR NEWSLETTER TO FIND OUT MORE.</div>
  <h2 class="abs">Australia's largest health charity implements Corvandel API Msg Bus</h2>
  <div class="abs nl-input">Entart &nbsp;Your Mail</div>
  <div class="btn nl-btn">SUBSCRIBE NOW</div>
</section>

<section class="section contact">
  <div class="abs contact-photo" role="img" aria-label="Smiling professional working on a laptop in a bright office"></div>
  <h2 class="abs">CONTACT US</h2>
  <div class="abs info" style="top:152px"><span class="ico"><svg width="14" height="14" viewBox="0 0 14 14"><path d="M3 1l2 3-1.5 1.5a8 8 0 0 0 5 5L10 9l3 2-1 2.5C6 13 1 8 .5 2z" fill="#fff"/></svg></span><div><b>PHONE :</b><span>+61 2 5550 0142</span></div></div>
  <div class="abs info" style="top:216px"><span class="ico"><svg width="14" height="12" viewBox="0 0 14 12"><rect x="0" y="1" width="14" height="10" fill="#fff"/><path d="M0 1l7 5 7-5" fill="none" stroke="#0b4a94" stroke-width="1.3"/></svg></span><div><b>MAIL :</b><span>hello@corvandel.com</span></div></div>

  <div class="abs form-panel">
    <h2 class="abs">GET IN TOUCH</h2>
    <div class="field" style="top:147px;left:42px;width:267px">Your name</div>
    <div class="field" style="top:147px;left:317px;width:267px">Phone</div>
    <div class="field" style="top:209px;left:42px;width:267px">Email address</div>
    <div class="field" style="top:209px;left:317px;width:267px">Subject</div>
    <div class="field" style="top:274px;left:42px;width:542px;height:91px">Message</div>
    <div class="btn form-btn">BOOK AN OBLIGATION FREE CONSULTATION WITH OUR LEAD TECHNOLOGIST</div>
  </div>
</section>

<footer class="section footer">
  <div class="abs brand" style="top:104px;left:112px"><span class="brand-square"></span>corvandel</div>
  <div class="abs social" aria-label="Social links"><i></i><i></i><i></i></div>
  <h3 class="abs" style="top:96px;left:457px">Quick links</h3>
  <ul class="abs links"><li>Home</li><li>About Us</li><li>Our Services</li><li>Blog</li><li>Contact Us</li></ul>
  <h3 class="abs" style="top:96px;left:665px">Subscribe for the latest content</h3>
  <div class="abs ft-text">Australia's Largest health charity implements Corvandel API Msg Bus</div>
  <div class="abs ft-input">Enter Email</div>
  <div class="btn ft-btn">SUBSCRIBE NOW</div>
  <div class="abs ft-rule"></div>
  <div class="centered ft-legal">Privacy Policy &nbsp;&nbsp;| &nbsp;&nbsp;Terms Of Use</div>
  <div class="centered ft-copy">© 2025 <b>CORVANDEL</b> All rights reserved.</div>
</footer>

</body>
</html>
```